Brand and Marketing Coach Needs PDF Designed

I have content that i need placed into a simple but great PDF design. The PDF is about the formula I use to build personal brands. This is geared towards entrepreneurs, experts, coaches, therapists, wellness practitioners, and indpendent business owners who serve to improve the lives of others.
The company name is changing from TorvelCast to Selling with the Village (I don't have that logo yet, so working backwards a bit. For now, the TorvelCast logo can be used.) My brand is NOT formal and corporate, but it's also not neon-pink and screaming at you. It's down to earth, hip, a bit modern but warm. It's about no BS and authenticity. The final deliverable should make the reader feel focused, smart, motivated and hopeful.

Target Market(s)

Conscious entrepreneurs and small business owners. this one is specifically for pharmacy entrepreneurs but this will be used for various audiences later.

Font styles to use
Sans Serif

Colors
eaf1f7
3377b5
6b449b
f37122
faa54b
f68e4e
ffc214

Requirements
Must have
• Modern design. colors that match logo - 4e5583 (i think that is the blue.) d65a40.
• Could have these colors as well: c6a254, 01bcc3
• But open to other colors
Nice to have
• I'd like to see some ways to make this PDF simple and readable, and eye-catching. I'd also like to use the uploaded ebooks for design ideas.
Should not have
• neon colors, clip art

```html
<!DOCTYPE html>
<html lang="en">
<head>
<meta charset="utf-8">
<title>The Signature Story Method – Spread Overview</title>
<link href="https://fonts.googleapis.com/css2?family=Cormorant+Garamond:ital,wght@0,400;0,500;0,600;1,400&family=Great+Vibes&family=Oswald:wght@400&family=Open+Sans:ital,wght@0,600;1,400&display=swap" rel="stylesheet">
<style>
  :root {
    --page-bg: #ffffff;
    --panel: #4f5684;
    --ink: #ffffff;
    --ink-soft: #eceef6;
    --serif: "Cormorant Garamond", Georgia, serif;
    --script: "Great Vibes", cursive;
    --display: "Oswald", "Arial Narrow", sans-serif;
    --sans: "Open Sans", Arial, sans-serif;
  }
  * { box-sizing: border-box; margin: 0; padding: 0; }
  html, body { width: 794px; height: 1200px; overflow: hidden; background: var(--page-bg); }
  .sheet { position: relative; width: 794px; height: 1200px; }

  .panel {
    position: absolute; width: 356px; height: 275px;
    background: var(--panel); color: var(--ink); overflow: hidden;
  }
  .col-a { left: 33px; } .col-b { left: 403px; }
  .row-1 { top: 27px; } .row-2 { top: 316px; } .row-3 { top: 607px; } .row-4 { top: 896px; }

  /* Cover */
  .cover-title {
    position: absolute; left: 0; right: 0; top: 78px; text-align: center;
    font: 400 30px/38px var(--display); letter-spacing: 2px;
  }
  .cover-audience { position: absolute; left: 0; right: 0; top: 203px; text-align: center; font: 600 12.5px/1 var(--sans); }
  .cover-tagline { position: absolute; left: 0; right: 0; top: 226px; text-align: center; font: italic 400 8.6px/12px var(--sans); color: var(--ink-soft); }

  /* Portrait page */
  .portrait {
    position: absolute; inset: 0;
    background:
      radial-gradient(ellipse 90px 120px at 52% 62%, #8a7a86 0%, #6a6689 55%, transparent 100%),
      linear-gradient(180deg, #353c6b 0%, #4a5283 40%, #4f5684 100%);
  }
  .story-line { position: absolute; left: 0; right: 0; top: 20px; text-align: center; font: 400 22px/1 var(--script); color: var(--ink); }

  /* Text pages */
  .kicker { position: absolute; left: 33px; top: 27px; font: italic 400 7.5px/1 var(--serif); color: var(--ink-soft); }
  .page-heading {
    position: absolute; left: 0; right: 0; top: 58px; text-align: center;
    font: 500 36px/1 var(--serif); font-variant: small-caps; letter-spacing: .5px;
  }
  .body-copy {
    position: absolute; left: 33px; right: 40px;
    font: 400 6.2px/7px var(--serif); color: var(--ink-soft);
  }
  .body-copy p { margin-bottom: 5.5px; }
  .intro-copy { top: 98px; }
  .body-copy .lead { font-size: 7.6px; line-height: 9px; margin-top: 2px; color: var(--ink); }
  .folio { position: absolute; left: 0; right: 0; top: 251px; text-align: center; font: 400 4.2px/1 var(--serif); letter-spacing: .3px; color: var(--ink-soft); }

  /* Section dividers */
  .section-number {
    position: absolute; left: 0; right: 0; text-align: center;
    font: 400 64px/1 var(--serif); font-variant-numeric: lining-nums;
  }
  .section-title { position: absolute; left: 0; right: 0; text-align: center; font: 400 33px/40px var(--serif); text-transform: uppercase; }
  .divider-1 .section-number { top: 76px; }
  .divider-1 .section-title { top: 154px; }
  .divider-2 .section-number { top: 46px; }
  .divider-2 .section-title { top: 123px; }

  .long-copy { top: 24px; }
  .long-copy .subhead { font-weight: 600; font-size: 8px; line-height: 8px; color: var(--ink); margin-bottom: 0; }
  .definition-copy { top: 36px; }
  .definition-copy .label { font-weight: 600; font-size: 7.6px; line-height: 8px; color: var(--ink); letter-spacing: .2px; margin-bottom: 0; }
  .pull-quote { text-align: center; font-style: italic; margin-top: 8px; }
  .pull-quote .attribution { display: block; font-style: normal; padding-left: 70px; }
  .pillars { text-align: center; margin-top: 6px; }
  .pillars li { list-style: none; font: 500 8px/20px var(--serif); letter-spacing: .6px; color: var(--ink); }
</style>
</head>
<body>
<main class="sheet">

  <section class="panel col-a row-1 cover">
    <h1 class="cover-title">THE SIGNATURE<br>STORY METHOD</h1>
    <p class="cover-audience">For Pharmacy Entrepreneurs</p>
    <p class="cover-tagline">The quick n' dirty guide to creating a unique personal brand<br>that attracts your ideal clients.</p>
  </section>

  <section class="panel col-b row-1 portrait-page">
    <div class="portrait" role="img" aria-label="Portrait photograph of the brand coach, seated and smiling, against a dark blue backdrop"></div>
    <p class="story-line">Your business has a story to tell.</p>
  </section>

  <section class="panel col-a row-2">
    <p class="kicker">I'm so glad you're here! Before we start, a few things:</p>
    <h2 class="page-heading">What this is:</h2>
    <div class="body-copy intro-copy">
      <p>The Signature Story Method consists of the exact steps I take to create unique and authentic brands for my clients. It is also what will drive your entire marketing strategy.</p>
      <p>One mistake I see entrepreneurs make is to consider BRAND as a separate entity from MARKETING. These two essential elements of your business are deeply connected.</p>
      <p>Rather than giving you the elements of a brand, which is really the end product of this work – what I'm giving you here are the essential building blocks, designed to help you discover and unleash your unique brand.</p>
      <p>This is what most people don't tell you about because it's the deep work that happens in the background.</p>
      <p>When you go through the steps to create your own brand, not only do you build a brand that attracts your ideal clients, but your marketing falls into place, and you finally learn what makes you stand way above the competition.</p>
      <p>Yes, it's true. When you take the time to create your brand, your messaging and marketing strategy fall into place. And this method is what gets you there.</p>
    </div>
    <p class="folio">PAGE X OF XX</p>
  </section>

  <section class="panel col-b row-2">
    <p class="kicker">I'm so glad you're here! Before we start, a few things:</p>
    <h2 class="page-heading">Who this is for:</h2>
    <div class="body-copy intro-copy">
      <p>The Signature Story Method is for you if you're a pharmacy entrepreneur who is starting or already running a business or practice. You may be moving a brick and mortar business online; creating a new business as a coach, patient advocate or navigator; or developing a service that will help your peers or patients.</p>
      <p>If you already have a business, you feel frustrated because you're not attracting your ideal clients – the type of clients you know you're meant to serve. And you don't know how you'll continue to expand your business.</p>
      <p>If you're in start-up, you understand that now is the time to nail down the right brand image and messaging so you can come out of the gate running, rather than wasting your precious time and money on tactics that don't work.</p>
      <p class="lead">Long story short, you're ready to step it up, get noticed, and grow your client base.</p>
    </div>
    <p class="folio">PAGE X OF XX</p>
  </section>

  <section class="panel col-a row-3 divider-1">
    <p class="section-number">1</p>
    <h2 class="section-title">Start Here</h2>
  </section>

  <section class="panel col-b row-3">
    <div class="body-copy long-copy">
      <p class="subhead">Freedom, impact, and profit…</p>
      <p>one or all of these are the reasons you started, or want to start, a business...</p>
      <p>But right now, you're wondering how you're going to stand out from all the online noise.</p>
      <p>Chatterly is supersaturated with experts and businesses offering very similar if not exactly the same things you do, which makes you doubt how doable and realistic this business thing really is.</p>
      <p>Naturally, when faced with this, you rush to create a logo, a website, and a presence on social media. And this is when I start to worry.</p>
      <p>Because that is COMPLETELY BACKWARDS!</p>
      <p>It's similar to a doctor prescribing medications to treat a patient's symptoms without identifying and understanding what is causing them. The symptoms could be side effects of another medicine, the results of illness, or could stem from any number of issues.</p>
      <p>Writing your website copy without knowing how to stand apart from others in your industry, position yourself as the expert, or the exact words and phrases that will get your ideal client's attention is a big waste of your time and money.</p>
      <p>When I see business owners do this, their eBook doesn't perform as they expected, their website is dead in the water, and they can't seem to get the right clients.</p>
      <p>What I do for my clients, before I can even begin thinking about their marketing, is to DEFINE them… figure out who they are, what they're about, and how to differentiate them so they'll stand out from all the online noise.</p>
      <p>This is the way to build a strong and authentic brand.</p>
    </div>
    <p class="folio">PAGE X OF XX</p>
  </section>

  <section class="panel col-a row-4 divider-2">
    <p class="section-number">2</p>
    <h2 class="section-title">What is<br>branding,<br>anyway?</h2>
  </section>

  <section class="panel col-b row-4">
    <div class="body-copy definition-copy">
      <p class="label">BRANDING IS NOT</p>
      <p>Branding is NOT your logo, colors, and fonts. That is visual branding, and you cannot create that until you have defined your brand.</p>
      <p class="label">BRANDING IS</p>
      <p>Branding is how you make someone feel after they've heard you talk, read your blog post, visited your website…</p>
      <p>Your brand has an essence, a personality, a definitive way of communicating. Your brand tells your story, speaks to your ideal client in a language they understand and causes them to have an emotional reaction.</p>
      <p class="pull-quote">"Your brand is what other people say about you when you're not in the room."<span class="attribution">– <strong>Marlowe Pratt</strong>, the founder of Shelfwise.com</span></p>
      <p style="margin-top:10px">When people know and trust your brand, they become clients. To have a credible and influential personal brand, you need to be able to articulate three things:</p>
      <ul class="pillars">
        <li>WHO YOU ARE</li>
        <li>WHAT YOU DO</li>
        <li>HOW YOU DO IT</li>
      </ul>
    </div>
    <p class="folio">PAGE X OF XX</p>
  </section>

</main>
</body>
</html>
```